Velk Partners Building Business Cards

We need a business card that reflects our business as "Solar Experts" in San Diego. Browse our website www.velkpartners.example our License needs to be displayed as "CSLB# 3867140" our phone number is (619) 555-0187

Save thousands on your electric bills and increase the value of your home while helping to protect the environment. Our solar installation experts will help you design the system that's right for you, using only the highest quality equipment that will look great and give you ideal performance. Our goal is to make you energy independent, and get your electric bill to 0.

Paul Osterby
(619) 555-0187
paul@velkpartners.example

Target Market(s)

Home owners in san diego looking for solar

Industry/Entity Type

Solar Energy

Contact Information for Business Card

Paul Osterby
(619) 555-0187
paul@velkpartners.example

Font styles to use
Other font styles liked:
• Use our logo font

Requirements
Must have
• License needs to be displayed as "CSLB# 3867140" our phone number is (619) 555-0187
Nice to have
• Real images of rooftop home solar in san diego
Should not have
• our business address

```html
<!DOCTYPE html>
<html lang="en">
<head>
<meta charset="utf-8">
<title>Velk Partners Building – Business Card</title>
<link rel="stylesheet" href="https://fonts.googleapis.com/css2?family=Roboto:wght@400;500;700&display=swap">
<style>
  :root {
    --page: #d9d4cd;
    --card-light: #edebe7;
    --brand-blue: #2d4a86;
    --brand-yellow: #e8a91c;
    --text-light: #f1ece4;
    --text-soft: #e3d9cc;
    --licence-number: #e0aeb0;
  }
  * { margin: 0; padding: 0; box-sizing: border-box; }
  html, body {
    width: 1200px; height: 1200px; overflow: hidden;
    background: var(--page);
    font-family: "Roboto", Arial, sans-serif;
  }
  .business-card {
    position: absolute; left: 100px; top: 303px;
    width: 1000px; height: 593px;
    background: var(--card-light);
    border-radius: 4px;
    overflow: hidden;
    box-shadow: 0 14px 40px rgba(60, 50, 40, 0.18);
  }
  .card-shapes { position: absolute; inset: 0; }
  .holder-name {
    position: absolute; left: 62px; top: 68px;
    font-size: 35px; font-weight: 700; color: var(--text-light);
    letter-spacing: -0.2px;
  }
  .holder-title {
    position: absolute; left: 62px; top: 114px;
    font-size: 23px; font-weight: 400; color: var(--text-soft);
  }
  .contact-list {
    position: absolute; left: 62px; top: 378px;
    list-style: none;
  }
  .contact-item {
    display: flex; align-items: center;
    height: 35px;
    font-size: 25px; color: var(--text-light);
  }
  .contact-icon { width: 26px; height: 22px; margin-right: 24px; flex: none; }
  .licence {
    position: absolute; left: 62px; top: 494px;
    font-size: 25px; color: var(--text-soft);
  }
  .licence-number { color: var(--licence-number); }
  .brand-mark {
    position: absolute; left: 690px; top: 250px; width: 290px;
    display: flex; align-items: center; gap: 14px;
    font-size: 26px; font-weight: 500; color: var(--brand-blue);
    line-height: 1.2;
  }
  .brand-dot {
    width: 38px; height: 38px; border-radius: 50%;
    background: var(--brand-yellow); flex: none;
  }
</style>
</head>
<body>
  <div class="business-card">
    <svg class="card-shapes" viewBox="0 0 1000 593" width="1000" height="593" aria-hidden="true">
      <path d="M0 0 H605 C520 140 500 420 605 593 H0 Z" fill="var(--brand-blue)"/>
      <path d="M622 0 H660 C575 110 548 260 545 380 C540 250 560 100 622 0 Z" fill="var(--brand-yellow)"/>
    </svg>

    <div class="holder-name">Paul Osterby</div>
    <div class="holder-title">Managing Director</div>

    <ul class="contact-list">
      <li class="contact-item">
        <svg class="contact-icon" viewBox="0 0 26 22" aria-hidden="true">
          <path d="M2 8 C2 2 24 2 24 8 L19 9 L18 6 C14 5 12 5 8 6 L7 9 Z" fill="var(--text-light)"/>
          <rect x="5" y="10" width="16" height="10" rx="2" fill="var(--text-light)"/>
          <circle cx="13" cy="15" r="2.6" fill="var(--brand-blue)"/>
        </svg>
        <span>(619) 555-0187</span>
      </li>
      <li class="contact-item">
        <svg class="contact-icon" viewBox="0 0 26 22" aria-hidden="true">
          <g fill="none" stroke="var(--text-light)" stroke-width="2">
            <circle cx="13" cy="11" r="9"/>
            <ellipse cx="13" cy="11" rx="4" ry="9"/>
            <line x1="4" y1="11" x2="22" y2="11"/>
          </g>
        </svg>
        <span>paul@velkpartners.example</span>
      </li>
      <li class="contact-item">
        <svg class="contact-icon" viewBox="0 0 26 22" aria-hidden="true">
          <rect x="2" y="4" width="22" height="15" fill="var(--text-light)"/>
          <path d="M2 4 L13 13 L24 4 M2 19 L10 11 M24 19 L16 11" fill="none" stroke="var(--brand-blue)" stroke-width="1.6"/>
        </svg>
        <span>www.velkpartners.example</span>
      </li>
    </ul>

    <div class="licence">License: CSLB# <span class="licence-number">3867140</span></div>

    <div class="brand-mark">
      <span class="brand-dot"></span>
      <span class="brand-name">Velk Partners Building</span>
    </div>
  </div>
</body>
</html>
```